New Business Card Design Project

I need a design for business cards, i am an electrical business called "Corvane Electrical and Communications" i need the cards to be double sided with the company logo on the back (attached) the front needs to say my company name, web site, email address, telephone number, and ABN number and electrical license number. I am open to different arrangements of the information but would like the background to be incorporating something electrical or something that looks smart. open to all additional ideas also.

The company colours are orange and grey see logo attached.

Business Name: Corvane Electrical and Communications
Website: corvaneelectricalandcomms.example.com.au
Email: brent@corvaneelectricalandcomms.example.com.au
Telephone(mobile): 0481209736
ABN: 71208349162
Lic No: 418273D

Target Market(s)

Business entities, Project Managers, Accounts, Clients

Industry/Entity Type

Electrician

Contact Information for Business Card

I need a design for business cards, i am an electrical business called "Corvane Electrical and Communications" i need the cards to be double sided with the company logo on the back (attached) the front needs to say my company name

Font styles to use
Serif
Sans Serif

Colors
f37122
5c5c5c

Requirements
Must have
• Must have the Logo on the back open to different ways of it being on the back but had in mind to keep it central but again open to other options
Nice to have
• A real modern cool background that is eye catching yet contemporary
Should not have
• No backgrounds of a light bulb or plug or anything like that

```html
<!DOCTYPE html>
<html lang="en">
<head>
<meta charset="utf-8">
<title>Corvane Electrical and Communications – Business Cards</title>
<link rel="stylesheet" href="https://fonts.googleapis.com/css2?family=Open+Sans:wght@400;600;700&display=swap">
<style>
  :root {
    --orange: #f37122;
    --amber: #f5a623;
    --grey: #5c5c5c;
    --charcoal: #4a4a4a;
    --charcoal-dark: #3c3c3c;
    --paper: #ffffff;
    --ink: #555555;
    --stage: #e6e6e6;
    --pale: #d9d9d9;
  }
  * { box-sizing: border-box; margin: 0; padding: 0; }
  html, body {
    width: 1200px; height: 950px; overflow: hidden;
    background: var(--stage);
    font-family: "Open Sans", Arial, sans-serif;
  }
  .card {
    position: absolute; left: 250px;
    width: 700px; height: 400px;
    border-radius: 4px; overflow: hidden;
    box-shadow: 0 6px 18px rgba(0,0,0,.18);
  }
  /* Back side */
  .card-back {
    top: 50px;
    background: linear-gradient(135deg, var(--grey) 0%, var(--charcoal) 55%, var(--charcoal-dark) 100%);
    display: flex; flex-direction: column; align-items: center; justify-content: center;
  }
  .brand-name {
    font-weight: 700; font-size: 64px; letter-spacing: 6px;
    color: var(--paper); line-height: 1;
  }
  .brand-tagline {
    margin-top: 10px;
    font-weight: 700; font-size: 15px; letter-spacing: 1.5px;
    color: var(--amber);
  }
  .back-website {
    margin-top: 34px;
    font-size: 15px; color: var(--pale); letter-spacing: .5px;
  }
  /* Front side */
  .card-front { top: 500px; background: var(--paper); }
  .front-panel { position: absolute; inset: 0; }
  .front-brand {
    position: absolute; left: 110px; top: 200px;
    width: 330px; transform: translate(-50%, -50%) rotate(-90deg);
    text-align: center;
  }
  .front-brand .brand-name { font-size: 54px; letter-spacing: 5px; }
  .front-brand .brand-tagline { font-size: 12px; margin-top: 8px; }
  .contact {
    position: absolute; left: 285px; top: 58px; right: 20px;
    color: var(--ink);
  }
  .person-name {
    font-weight: 700; font-size: 20px; letter-spacing: 1px;
    color: var(--amber); line-height: 1.1;
  }
  .person-role { font-size: 14px; letter-spacing: 1px; margin-top: 2px; }
  .registration { margin-top: 62px; font-size: 15px; line-height: 1.45; }
  .contact-list { list-style: none; margin-top: 8px; font-size: 15px; }
  .contact-list li { display: flex; align-items: center; gap: 8px; line-height: 1.6; }
  .contact-list svg { flex: none; }
</style>
</head>
<body>

<section class="card card-back" aria-label="Card back">
  <div class="brand-name">CORVANE</div>
  <div class="brand-tagline">ELECTRICAL &amp; COMMUNICATIONS</div>
  <div class="back-website">corvaneelectricalandcomms.example.com.au</div>
</section>

<section class="card card-front" aria-label="Card front">
  <svg class="front-panel" width="700" height="400" viewBox="0 0 700 400" aria-hidden="true">
    <defs>
      <linearGradient id="panelShade" x1="0" y1="0" x2="1" y2="1">
        <stop offset="0" stop-color="#5c5c5c"/>
        <stop offset="1" stop-color="#444444"/>
      </linearGradient>
    </defs>
    <path d="M0 0 H255 C195 35 265 85 215 125 C165 165 265 205 220 250 C180 290 250 330 225 400 H0 Z" fill="url(#panelShade)"/>
    <path d="M255 0 C195 35 265 85 215 125 C165 165 265 205 220 250 C180 290 250 330 225 400" fill="none" stroke="var(--amber)" stroke-width="5" stroke-linecap="round"/>
  </svg>

  <div class="front-brand">
    <div class="brand-name">CORVANE</div>
    <div class="brand-tagline">ELECTRICAL &amp; COMMUNICATIONS</div>
  </div>

  <div class="contact">
    <div class="person-name">MARCUS HALE</div>
    <div class="person-role">PRESIDENT</div>
    <div class="registration">
      <div>ABN: 71208349162</div>
      <div>Lic No: 418273D</div>
    </div>
    <ul class="contact-list">
      <li>
        <svg width="14" height="18" viewBox="0 0 14 18" aria-label="Phone"><rect x="1" y="1" width="12" height="16" rx="2" fill="none" stroke="var(--amber)" stroke-width="2"/><circle cx="7" cy="14" r="1.2" fill="var(--amber)"/></svg>
        <span>0481209736</span>
      </li>
      <li>
        <svg width="16" height="12" viewBox="0 0 16 12" aria-label="Email"><rect x="0" y="0" width="16" height="12" rx="1.5" fill="var(--amber)"/><path d="M1 1.5 L8 7 L15 1.5" fill="none" stroke="#fff" stroke-width="1.4"/></svg>
        <span>brent@corvaneelectricalandcomms.example.com.au</span>
      </li>
      <li>
        <svg width="16" height="16" viewBox="0 0 16 16" aria-label="Website"><circle cx="8" cy="8" r="8" fill="var(--amber)"/><ellipse cx="8" cy="8" rx="3.2" ry="7" fill="none" stroke="#fff" stroke-width="1.1"/><path d="M1 8 H15" stroke="#fff" stroke-width="1.1"/></svg>
        <span>corvaneelectricalandcomms.example.com.au</span>
      </li>
    </ul>
  </div>
</section>

</body>
</html>
```